Velk Partners Building Business Cards

We need a business card that reflects our business as "Solar Experts" in San Diego. Browse our website www.velkpartners.example our License needs to be displayed as "CSLB# 3867140" our phone number is (619) 555-0187

Save thousands on your electric bills and increase the value of your home while helping to protect the environment. Our solar installation experts will help you design the system that's right for you, using only the highest quality equipment that will look great and give you ideal performance. Our goal is to make you energy independent, and get your electric bill to 0.

Paul Osterby
(619) 555-0187
paul@velkpartners.example

Target Market(s)

Home owners in san diego looking for solar

Industry/Entity Type

Solar Energy

Contact Information for Business Card

Paul Osterby
(619) 555-0187
paul@velkpartners.example

Font styles to use
Other font styles liked:
• Use our logo font

Requirements
Must have
• License needs to be displayed as "CSLB# 3867140" our phone number is (619) 555-0187
Nice to have
• Real images of rooftop home solar in san diego
Should not have
• our business address

```html
<!DOCTYPE html>
<html lang="en">
<head>
<meta charset="utf-8">
<title>Velk Partners Building – Business Card</title>
<link rel="stylesheet" href="https://fonts.googleapis.com/css2?family=Source+Sans+3:wght@400;600;700&display=swap">
<style>
  :root {
    --stage-top: #8e8e8e;
    --stage-bottom: #a4a4a4;
    --card-white: #ffffff;
    --navy: #1c3474;
    --navy-deep: #1a3272;
    --sun: #f5b00f;
    --ink: #222a3a;
    --white: #ffffff;
  }
  * { margin: 0; padding: 0; box-sizing: border-box; }
  html, body { width: 1200px; height: 900px; overflow: hidden; }
  body {
    background: linear-gradient(180deg, var(--stage-top) 0%, var(--stage-bottom) 100%);
    font-family: "Source Sans 3", "Myriad Pro", Arial, sans-serif;
    position: relative;
  }
  .card {
    position: absolute;
    top: 306px;
    width: 440px;
    height: 271px;
    border-radius: 12px;
    box-shadow: 0 1px 3px rgba(0,0,0,0.18);
    overflow: hidden;
  }
  .card-front { left: 149px; background: var(--card-white); }
  .card-back { left: 608px; background: var(--navy-deep); }

  .brand-mark {
    position: absolute;
    left: 36px;
    top: 108px;
    display: flex;
    align-items: center;
    gap: 10px;
  }
  .brand-dot {
    width: 44px; height: 44px;
    border-radius: 50%;
    background: var(--sun);
    flex: none;
  }
  .brand-name {
    font-weight: 700;
    font-size: 19px;
    line-height: 1.1;
    color: var(--navy);
    width: 130px;
  }

  .contact-block {
    position: absolute;
    left: 249px;
    top: 0;
  }
  .person-name {
    position: absolute;
    top: 62px;
    font-size: 15px;
    font-weight: 600;
    color: var(--navy);
    text-transform: uppercase;
    white-space: nowrap;
    letter-spacing: 0.1px;
  }
  .contact-list {
    position: absolute;
    top: 123px;
    list-style: none;
    font-size: 12.5px;
    color: var(--ink);
    white-space: nowrap;
  }
  .contact-list li {
    display: flex;
    align-items: center;
    gap: 5px;
    height: 16px;
  }
  .contact-list svg { width: 10px; height: 8px; fill: var(--navy); flex: none; }
  .license {
    position: absolute;
    top: 192px;
    font-size: 12.5px;
    color: var(--ink);
    white-space: nowrap;
  }
  .license strong { color: var(--navy); font-weight: 700; }

  .back-name {
    position: absolute;
    left: 0; right: 0;
    top: 106px;
    text-align: center;
    font-weight: 700;
    font-size: 36px;
    line-height: 1;
    color: var(--white);
    letter-spacing: -0.5px;
  }
</style>
</head>
<body>
  <section class="card card-front" aria-label="Business card front">
    <div class="brand-mark">
      <span class="brand-dot" aria-hidden="true"></span>
      <span class="brand-name">Velk Partners Building</span>
    </div>
    <div class="contact-block">
      <h1 class="person-name">Paul Osterby</h1>
      <ul class="contact-list">
        <li>
          <svg viewBox="0 0 10 8" aria-hidden="true"><path d="M0 2.2C1.5 0.6 3.3 0 5 0s3.5 0.6 5 2.2L8.6 3.4 7.2 2.6V1.8C6.5 1.5 5.8 1.4 5 1.4S3.5 1.5 2.8 1.8v0.8L1.4 3.4zM2.6 3.6h4.8L9 7.6H1z"/></svg>
          (619) 555-0187
        </li>
        <li>
          <svg viewBox="0 0 10 8" aria-hidden="true"><path d="M0 0.8h10v0.6L5 4.6 0 1.4zM0 2.4l5 3.2 5-3.2V7.2H0z"/></svg>
          paul@velkpartners.example
        </li>
      </ul>
      <p class="license"><strong>License:</strong> CSLB# 3867140</p>
    </div>
  </section>

  <section class="card card-back" aria-label="Business card back">
    <p class="back-name">Velk Partners Building</p>
  </section>
</body>
</html>
```